Brightwave Reach - Business Card

We need a business card for a Social Media Marketing company that specializes in online marketing for small businesses in Canada using common Social Media platforms such as Pixlora, Chatterly, Blinkpost & Quibber.

I have uploaded a copy of our logo which I would like utilized in the business card. We would like the business card to be modern yet classy design.

Our website is www.brightwavereach.ca

Industry/Entity Type

Marketing

Contact Information for Business Card

Email: info@brightwavereach.ca
Website: www.brightwavereach.ca
Telephone: 604-555-0193

Colors

Designer to choose colors to be used in the design.

Requirements
Must have
• Social Media icons on reverse
• Please add some designs with color.

```html
<!DOCTYPE html>
<html lang="en">
<head>
<meta charset="utf-8">
<title>Brightwave Reach – Business Card</title>
<link href="https://fonts.googleapis.com/css2?family=Questrial&display=swap" rel="stylesheet">
<style>
  :root {
    --page-bg: #f4f4f4;
    --card-dark: #1c1d1f;
    --card-mid: #2e3033;
    --silver: #d9d9d9;
    --silver-soft: #bdbdbd;
    --silver-dim: #9a9a9a;
    --band-light: #f2f2f2;
    --band-dark: #6d6d6d;
    --accent: #d6312b;
    --accent-deep: #9e1f1b;
  }
  * { margin: 0; padding: 0; box-sizing: border-box; }
  html, body {
    width: 1200px;
    height: 900px;
    overflow: hidden;
    background: var(--page-bg);
    font-family: "Questrial", sans-serif;
  }
  .stage { position: relative; width: 1200px; height: 900px; }
  .card {
    position: absolute;
    top: 290px;
    width: 530px;
    height: 320px;
    border-radius: 24px;
    overflow: hidden;
    box-shadow: 0 18px 30px rgba(0,0,0,0.2);
  }
  .card-front { left: 40px; }
  .card-back { left: 630px; }
  .card-surface {
    position: absolute;
    inset: 0;
    background: radial-gradient(ellipse at 50% 40%, var(--card-mid) 0%, var(--card-dark) 75%);
  }
  .accent-edge {
    position: absolute;
    left: 0;
    right: 0;
    bottom: 0;
    height: 5px;
    background: linear-gradient(90deg, var(--accent-deep), var(--accent), var(--accent-deep));
  }
  .brand-name {
    position: absolute;
    left: 0;
    right: 0;
    text-align: center;
    color: var(--silver);
    text-transform: uppercase;
    letter-spacing: 1px;
    line-height: 1.02;
  }
  .card-front .brand-name { top: 46px; font-size: 30px; }
  .card-back .brand-name { top: 80px; font-size: 40px; }
  .brand-mark {
    display: block;
    margin: 10px auto 0;
    width: 12px;
    height: 12px;
    background: var(--accent);
  }
  .card-back .brand-mark { width: 14px; height: 14px; margin-top: 14px; }
  .divider-band {
    position: absolute;
    left: 0;
    right: 0;
    top: 160px;
    height: 6px;
    background: linear-gradient(180deg, var(--band-light) 0%, var(--silver-soft) 50%, var(--band-dark) 100%);
  }
  .contact-list {
    position: absolute;
    left: 0;
    right: 0;
    top: 198px;
    text-align: center;
    list-style: none;
    color: var(--silver-soft);
  }
  .contact-phone { font-size: 20px; letter-spacing: 1.5px; color: var(--silver); margin-bottom: 6px; }
  .contact-email { font-size: 16px; letter-spacing: 0.5px; margin-bottom: 6px; }
  .contact-web { font-size: 16px; letter-spacing: 0.8px; color: var(--silver-dim); }
  .social-list {
    position: absolute;
    left: 0;
    right: 0;
    top: 252px;
    display: flex;
    justify-content: center;
    gap: 18px;
    list-style: none;
    font-size: 12px;
    letter-spacing: 0.6px;
    color: var(--silver-soft);
  }
  .social-item { display: flex; align-items: center; gap: 6px; }
  .social-square {
    width: 16px;
    height: 16px;
    border-radius: 4px;
    background: var(--accent);
  }
</style>
</head>
<body>
<main class="stage">
  <section class="card card-front" aria-label="Card front">
    <div class="card-surface"></div>
    <p class="brand-name">Brightwave<br>Reach<span class="brand-mark"></span></p>
    <div class="divider-band"></div>
    <ul class="contact-list">
      <li class="contact-phone">604-555-0193</li>
      <li class="contact-email">info@brightwavereach.ca</li>
      <li class="contact-web">www.brightwavereach.ca</li>
    </ul>
    <div class="accent-edge"></div>
  </section>

  <section class="card card-back" aria-label="Card back">
    <div class="card-surface"></div>
    <p class="brand-name">Brightwave<br>Reach<span class="brand-mark"></span></p>
    <ul class="social-list">
      <li class="social-item"><span class="social-square"></span>Pixlora</li>
      <li class="social-item"><span class="social-square"></span>Chatterly</li>
      <li class="social-item"><span class="social-square"></span>Blinkpost</li>
      <li class="social-item"><span class="social-square"></span>Quibber</li>
    </ul>
    <div class="accent-edge"></div>
  </section>
</main>
</body>
</html>
```